Travel Agency Website - Simple General

Need a 7 page simple design that is pretty repetitive. Need to be able to load quickly that is SEO optimized. Trying to give ideas on what they can do, be personal as we are local, but at the same time come across as professional and get information easily with little burden.

- Landing Page
- Brimwell Vacations Page
- Family Trips
- Road Trips from Texas
- Other Destinations
- About Us Page
- Contact Us Page

Target Market(s)

Families

Coding

Coded - Design and coding required

Number of Pages Required

5+ page

Colors

Designer to choose colors to be used in the design.

Requirements
Must have
• Like it to flow easily with our logo. Use that for colors, etc.

```html
<!DOCTYPE html>
<html lang="en">
<head>
<meta charset="utf-8">
<title>Hum Along Travels – Your Local Guide</title>
<link href="https://fonts.googleapis.com/css2?family=Inter:wght@400;500;600;700&family=Lobster&family=Yellowtail&display=swap" rel="stylesheet">
<style>
:root{
  --teal:#1f5d73;
  --teal-dark:#1b4b5a;
  --ink:#111;
  --body:#333;
  --grey-band:#f1f1f1;
  --icon:#b9b9b9;
  --white:#fff;
}
*{margin:0;padding:0;box-sizing:border-box}
html,body{width:1200px;height:4033px;overflow:hidden;background:var(--white)}
body{position:relative;font-family:Inter,sans-serif;color:var(--body)}
.abs{position:absolute}

/* hero */
.hero{left:0;top:0;width:1200px;height:721px;background:linear-gradient(180deg,#2a8fd6 0%,#3fb0e6 30%,#1aa6d8 55%,#35c3e8 80%,#7fdcf2 100%)}
.hero-palms{left:760px;top:0;width:440px;height:380px;background:radial-gradient(ellipse at 70% 40%,#2f7a3a 0%,#3f8f44 40%,rgba(60,140,70,0) 72%)}
.brand{left:20px;top:40px;display:flex;align-items:center;gap:8px;color:var(--white);font-weight:700;font-size:17px}
.brand .dot{width:26px;height:26px;border-radius:50%;background:var(--white)}
.nav{left:235px;top:68px;display:flex;gap:20px;font-size:13px;color:var(--white)}
.nav a{color:inherit;text-decoration:none;padding-bottom:6px}
.nav a.active{font-weight:600;border-bottom:2px solid var(--white)}
.nav-cta{left:1054px;top:61px;width:123px;height:32px;border-radius:16px;background:var(--white);color:var(--ink);font-size:13px;display:flex;align-items:center;justify-content:center}
.hero-title{left:0;top:180px;width:1200px;text-align:center;font-family:Yellowtail,cursive;font-size:170px;line-height:1;color:var(--white);-webkit-text-stroke:3px #0d2b33;letter-spacing:2px}
.hero-sub{left:0;top:395px;width:1200px;text-align:center;font-family:Lobster,cursive;font-size:66px;line-height:86px;color:#0b0b0b}
.hero-pill{left:475px;top:588px;width:250px;height:38px;border-radius:19px;background:rgba(255,255,255,.7);font-size:21px;color:#2a4a55;display:flex;align-items:center;justify-content:center}
.slider{left:537px;top:693px;width:126px;height:56px;background:var(--white);border-radius:4px;box-shadow:0 3px 10px rgba(0,0,0,.2);display:flex}
.slider span{flex:1;display:flex;align-items:center;justify-content:center}
.slider span+span{border-left:1px solid #ddd}

/* about */
.about{left:103px;top:822px;width:980px}
.about h1{font-size:34px;font-weight:500;color:var(--teal)}
.about .rule{margin-top:12px;width:412px;border-top:2px dotted #999}
.about p{font-size:12.5px;line-height:20px;color:var(--body);margin-top:22px}
.about p:first-of-type{margin-top:24px}
.about b{color:var(--ink)}

/* offer rows */
.offer h2{font-size:27px;font-weight:500;color:var(--teal);line-height:1.2}
.offer .partner{font-size:15px;color:var(--teal);margin-top:6px}
.offer p{font-size:12.5px;line-height:20px;color:var(--ink);margin-top:14px}
.offer .partner+p{color:var(--teal)}
.btn-sm{display:inline-flex;align-items:center;gap:6px;margin-top:20px;height:31px;padding:0 12px;background:var(--teal-dark);color:var(--white);font-size:12.5px;border-radius:3px}
.photo{border:4px solid var(--white);box-shadow:0 0 6px rgba(0,0,0,.25)}

/* feature band */
.feature{left:0;top:3436px;width:1200px;height:403px;background:var(--grey-band)}
.feature h2{position:absolute;left:114px;top:34px;width:500px;font-size:46px;font-weight:500;color:var(--ink);line-height:54px}
.feature p{position:absolute;left:114px;top:172px;width:460px;font-size:16px;line-height:24px;color:var(--ink)}
.feature .btn-lg{position:absolute;left:114px;top:295px;width:217px;height:50px;background:var(--teal-dark);color:var(--white);font-size:14px;display:flex;align-items:center;justify-content:center;border-radius:2px}
.map{left:658px;top:49px;width:430px;height:307px;border:2px solid #6d86a5;background:linear-gradient(135deg,#f3e07a 0%,#f2a4b8 35%,#a8d98a 60%,#8fc9ea 100%)}

/* footer */
.footer{left:0;top:3839px;width:1200px;height:194px;border-top:1px solid #ddd}
.footer .brand-f{left:34px;top:66px;display:flex;align-items:center;gap:8px;font-size:17px;font-weight:700;color:var(--teal)}
.footer .brand-f .dot{width:24px;height:24px;border-radius:50%;background:var(--teal)}
.fcol{display:flex;flex-direction:column;gap:11px;font-size:13px;color:var(--ink)}
.socials{display:flex;gap:12px;margin-top:2px}
.socials span{width:18px;height:18px;border-radius:4px;background:#777}
</style>
</head>
<body>

<header>
  <div class="abs hero" role="img" aria-label="Turquoise infinity pool meeting the ocean with palm trees on the right"></div>
  <div class="abs hero-palms"></div>
  <div class="abs brand"><span class="dot"></span>Hum Along</div>
  <nav class="abs nav">
    <a class="active">Home</a><a>Brimwell Vacations</a><a>Family Trips</a><a>Road Trips from Texas</a><a>Other Destinations</a><a>About Us</a><a>Contact Us</a>
  </nav>
  <div class="abs nav-cta">Book Now!</div>
  <div class="abs hero-title">Big Adventure</div>
  <div class="abs hero-sub">Hum Along Travels<br>Your local Guide</div>
  <div class="abs hero-pill">Book your Destination</div>
  <div class="abs slider">
    <span><svg width="24" height="24" viewBox="0 0 24 24" fill="none" stroke="#1f5d73" stroke-width="2"><path d="M20 12H4M10 6l-6 6 6 6"/></svg></span>
    <span><svg width="24" height="24" viewBox="0 0 24 24" fill="none" stroke="#1f5d73" stroke-width="2"><path d="M4 12h16M14 6l6 6-6 6"/></svg></span>
  </div>
</header>

<section class="abs about">
  <h1>About Us Hum Along</h1>
  <div class="rule"></div>
  <p>Turn your travel dreams into seamless, unforgettable experiences. At <b>Hum Along Travels</b>, we believe planning your trip should feel just as exciting as the journey itself not overwhelming.</p>
  <p>From magical theme park adventures and relaxing beach escapes to scenic road trips and hidden destination gems, we take care of every detail so you can focus on making memories. Whether you're traveling with family, friends, or planning a solo escape, we create personalized itineraries tailored to your style, budget, and pace.</p>
  <p><b>No stress. No confusion. Just smooth</b>, well-planned travel from start to finish.</p>
</section>

<!-- Brimwell -->
<div class="abs offer" style="left:106px;top:1207px;width:460px">
  <svg width="70" height="70" viewBox="0 0 24 24" fill="var(--icon)"><path d="M21 3c-1-1-3 0-4 1l-3 3-8-2-2 2 6 4-3 3-3-1-1 1 3 2 2 3 1-1-1-3 3-3 4 6 2-2-2-8 3-3c1-1 2-3 1-4z"/></svg>
  <h2 style="margin-top:30px">Brimwell Vacations – Land and Sea</h2>
  <p>Experience the magic on land and cruise the seas with perfectly<br>planned Brimwell adventures.</p>
  <div class="btn-sm"><svg width="12" height="12" viewBox="0 0 24 24" fill="#fff"><path d="M22 2L2 10l8 3 3 8z"/></svg>Book Now!</div>
</div>
<div class="abs photo" style="left:641px;top:1144px;width:435px;height:449px;background:linear-gradient(180deg,#3d86e0 0%,#5aa0ea 45%,#6a6a6a 70%,#8a5540 100%)" role="img" aria-label="Theme park entrance gate with visitors walking in"></div>
<div class="abs photo" style="left:967px;top:1440px;width:169px;height:240px;background:linear-gradient(180deg,#3a9fe0 0%,#a9dcf4 45%,#47c7d8 70%,#29b4c7 100%)" role="img" aria-label="White cruise ship on calm turquoise sea"></div>

<!-- Family -->
<div class="abs photo" style="left:100px;top:1785px;width:440px;height:448px;background:linear-gradient(160deg,#e9f0f3 0%,#c9dbe2 40%,#8fb4c4 70%,#b9a18f 100%)" role="img" aria-label="Family with children pulling suitcases"></div>
<div class="abs offer" style="left:640px;top:1846px;width:460px">
  <svg width="40" height="82" viewBox="0 0 20 40" fill="var(--icon)"><rect x="2" y="0" width="2" height="14" transform="rotate(-15 3 7)"/><rect x="7" y="12" width="11" height="24" rx="2" transform="rotate(-15 12 24)"/></svg>
  <h2 style="margin-top:4px">Family Trips</h2>
  <p>Create lifelong memories with customized trips designed for all ages.</p>
  <div class="btn-sm"><svg width="12" height="12" viewBox="0 0 24 24" fill="#fff"><path d="M22 2L2 10l8 3 3 8z"/></svg>Book Now!</div>
</div>

<!-- Texas -->
<div class="abs offer" style="left:106px;top:2424px;width:500px">
  <svg width="88" height="44" viewBox="0 0 44 22" fill="var(--icon)"><path d="M4 8h6l4-6h14l6 6h6a3 3 0 013 3v5H1v-5a3 3 0 013-3z"/><circle cx="11" cy="17" r="4" fill="#fff" stroke="var(--icon)" stroke-width="2"/><circle cx="33" cy="17" r="4" fill="#fff" stroke="var(--icon)" stroke-width="2"/></svg>
  <h2 style="margin-top:16px">Texas – Road Trip</h2>
  <div class="partner">(Partnership with Pineyway Van Rentals)</div>
  <p>Hit the road and explore Texas with flexible, fun, and comfortable van travel.</p>
  <div class="btn-sm"><svg width="12" height="12" viewBox="0 0 24 24" fill="#fff"><path d="M22 2L2 10l8 3 3 8z"/></svg>Book Now!</div>
</div>
<div class="abs photo" style="left:655px;top:2332px;width:440px;height:449px;background:linear-gradient(180deg,#a9c4d8 0%,#d9e3ea 25%,#9a5a3a 50%,#c79a6c 70%,#6e6c6a 100%)" role="img" aria-label="Desert highway leading toward red rock buttes"></div>

<!-- Other -->
<div class="abs photo" style="left:136px;top:2885px;width:441px;height:449px;background:linear-gradient(180deg,#5cb2ec 0%,#9fd0f2 50%,#c89a5a 75%,#b8302e 100%)" role="img" aria-label="Hand holding a suitcase with a straw hat, airplane in the sky"></div>
<div class="abs offer" style="left:642px;top:2971px;width:460px">
  <svg width="82" height="50" viewBox="0 0 41 25" fill="var(--icon)"><path d="M28 24c0-8 2-14 6-18l1 1c-3 4-5 10-5 17z"/><path d="M34 6c-4-3-9-2-11 1 3-1 6-1 9 1-3 0-6 2-7 4 3-2 6-2 9-1-1-2 0-4 0-5 3 1 6 4 6 6 0-3-2-6-6-6z"/><path d="M0 24c8-4 20-4 40 0z"/><circle cx="10" cy="14" r="3"/></svg>
  <h2 style="margin-top:12px">Other Destinations</h2>
  <p>Discover unique destinations worldwide tailored to your travel dreams.</p>
  <div class="btn-sm"><svg width="12" height="12" viewBox="0 0 24 24" fill="#fff"><path d="M22 2L2 10l8 3 3 8z"/></svg>Book Now!</div>
</div>

<!-- Feature -->
<section class="abs feature">
  <h2>Feature Destination on the map</h2>
  <p>Lorem ipsum dolor sit amet, consectetur adipiscing elit, sed do eiusmod tempor incididunt ut labore et dolore magna aliqua.</p>
  <div class="btn-lg">Get Quote Now!</div>
  <div class="abs map" role="img" aria-label="Colour map of the United States"></div>
</section>

<footer class="abs footer">
  <div class="abs brand-f"><span class="dot"></span>Hum Along</div>
  <div class="abs fcol" style="left:320px;top:40px"><span>Home</span><span>About Us</span><span>Contact Us</span></div>
  <div class="abs fcol" style="left:586px;top:40px"><span>Brimwell Vacations</span><span>Family Trips</span><span>Road Trips from Texas</span><span>Other Destinations</span></div>
  <div class="abs fcol" style="left:893px;top:40px"><span>hello@humalongtravels.com</span><span>01 - 555 010 2233</span><div class="socials"><span></span><span></span><span></span></div></div>
</footer>

</body>
</html>
```